Stationary design for boutique production house

We need a stationary design for our production house, 'Lorno Productions' based in Singapore. We produce microfilms as well as podcasts, talkshows and events. Our logo is a stylized icon of our director, who is also the executive producer and host of our programs, Lorno. Our main company colors are Red, Black and white. We would like a clean, minimalist design incorporating our existing company logo that conveys a sense of urbanism and elegance.

Logo and font files are attached. f

Target Market(s)

We focus on lifestyle media rather than entertainment.

Industry/Entity Type

Boutique

Font styles to use
Serif
Sans Serif

Colors
ec1f27
ffffff
000000

Requirements
Must have
• Our company logo and at least one of our company colors.
Nice to have
• Our address and contact information.
Should not have
• Changes made to the company logo (using only certain parts of it is fine though)

```html
<!DOCTYPE html>
<html lang="en">
<head>
<meta charset="utf-8">
<title>Lorno Productions – Business Cards</title>
<link rel="stylesheet" href="https://fonts.googleapis.com/css2?family=Bodoni+Moda:wght@500&family=Jost:wght@400&display=swap">
<style>
  :root {
    --brand-red: #ec1f27;
    --ink: #1e1b1c;
    --paper: #ffffff;
    --muted: #4a4a4a;
    --backdrop: #e9e9e9;
    --serif: "Bodoni Moda", "Didot", serif;
    --sans: "Jost", "Futura", sans-serif;
  }
  * { box-sizing: border-box; margin: 0; padding: 0; }
  html, body { width: 1200px; height: 659px; overflow: hidden; }
  body {
    background: var(--backdrop);
    font-family: var(--sans);
    display: flex;
    align-items: center;
    justify-content: center;
    gap: 60px;
  }
  .card {
    width: 300px;
    height: 525px;
    position: relative;
    overflow: hidden;
    box-shadow: 0 6px 18px rgba(0,0,0,0.18);
  }
  .brand-name {
    font-family: var(--serif);
    font-weight: 500;
    font-size: 22px;
    line-height: 1.05;
    letter-spacing: 0.5px;
    text-transform: uppercase;
    text-align: center;
  }
  .rule {
    width: 150px;
    height: 1px;
    position: relative;
  }
  .rule::before, .rule::after {
    content: "";
    position: absolute;
    top: -2px;
    width: 5px; height: 5px;
    border-radius: 50%;
  }
  .rule::before { left: 0; }
  .rule::after { right: 0; }

  /* Front */
  .card-front {
    background: var(--paper);
    padding-top: 58px;
    display: flex;
    flex-direction: column;
    align-items: center;
  }
  .brand-mark {
    width: 104px; height: 104px;
    border-radius: 50%;
    background: var(--ink);
    margin-bottom: 16px;
  }
  .card-front .brand-name { color: var(--ink); }
  .card-front .rule { background: var(--ink); margin: 12px 0 30px; }
  .card-front .rule::before, .card-front .rule::after { background: var(--brand-red); }

  .contact { width: 190px; }
  .person-name {
    color: var(--brand-red);
    font-size: 16px;
    letter-spacing: 0.5px;
    text-transform: uppercase;
  }
  .person-role {
    color: var(--ink);
    font-size: 12px;
    letter-spacing: 0.5px;
    margin-bottom: 12px;
  }
  .address {
    color: var(--muted);
    font-size: 11px;
    line-height: 1.5;
    margin-bottom: 6px;
  }
  .contact-list { list-style: none; }
  .contact-list li {
    display: flex;
    align-items: center;
    gap: 8px;
    color: var(--muted);
    font-size: 11px;
    line-height: 1.7;
    letter-spacing: 0.3px;
  }
  .contact-list svg { width: 11px; height: 11px; flex: none; fill: var(--brand-red); }

  /* Back */
  .card-back {
    background: var(--brand-red);
    padding-top: 60px;
    display: flex;
    flex-direction: column;
    align-items: center;
    color: var(--paper);
  }
  .card-back .brand-name { color: var(--paper); font-size: 24px; }
  .card-back .rule { background: var(--paper); margin: 12px 0 8px; }
  .card-back .rule::before, .card-back .rule::after { background: var(--paper); }
  .back-web {
    font-size: 11px;
    letter-spacing: 2px;
  }
  .back-mark {
    position: absolute;
    width: 400px; height: 400px;
    border-radius: 50%;
    background: var(--paper);
    left: 10px;
    top: 250px;
  }
</style>
</head>
<body>

  <article class="card card-front">
    <span class="brand-mark"></span>
    <h1 class="brand-name">Lorno<br>Productions</h1>
    <div class="rule"></div>

    <div class="contact">
      <p class="person-name">Alec Morrow</p>
      <p class="person-role">CEO/FOUNDER</p>
      <p class="address">2140 Harbour Row<br>Singapore 049315</p>
      <ul class="contact-list">
        <li><svg viewBox="0 0 12 12"><path d="M2.5 1 4.5 1 5.3 3.6 4 4.6C4.7 6 6 7.3 7.4 8L8.4 6.7 11 7.5 11 9.5C11 10.3 10.3 11 9.5 11 5 11 1 7 1 2.5 1 1.7 1.7 1 2.5 1Z"/></svg>612 408 3175</li>
        <li><svg viewBox="0 0 12 12"><path d="M3.5 0.5h5a1 1 0 0 1 1 1v9a1 1 0 0 1-1 1h-5a1 1 0 0 1-1-1v-9a1 1 0 0 1 1-1Zm0.5 1.5v7h4v-7Z"/></svg>612 408 3176</li>
        <li><svg viewBox="0 0 12 12"><path d="M3 1h6v3H3Z M1 5h10v5H9V8H3v2H1Z M3.5 9h5v2h-5Z"/></svg>612 408 3177</li>
        <li><svg viewBox="0 0 12 12"><path d="M1 2.5h10v7H1Z M1.8 3.3 6 6.5 10.2 3.3" stroke="#fff" stroke-width="0.8"/></svg>hello@lornoprod.sg</li>
        <li><svg viewBox="0 0 12 12"><circle cx="6" cy="6" r="5"/><path d="M1 6h10M6 1c-2.2 2.8-2.2 7.2 0 10M6 1c2.2 2.8 2.2 7.2 0 10" stroke="#fff" stroke-width="0.7" fill="none"/></svg>www.lornoprod.sg</li>
      </ul>
    </div>
  </article>

  <article class="card card-back">
    <h2 class="brand-name">Lorno<br>Productions</h2>
    <div class="rule"></div>
    <p class="back-web">www.lornoprod.sg</p>
    <span class="back-mark"></span>
  </article>

</body>
</html>
```